Website for my photography business

I need a website for my photography business, Bram Kellet Photography. I need a website that has a landing page with a cover photo of each kind of photography I do. For example, Nature, Weddings, Portraits and Architecture. I want it so that when someone comes onto my website they have to choose which kind of photography page they want to visit. So if they click on the wedding photo it will open to a page with my wedding portfolio images and a contact me button. If they choose nature photography I want them to be redirected to an e-commerce section where they can purchase prints. Architecture and Portraits should open up to their respective portfolios with about me and contact info. I like this kind of format because I want people who come to my website for a specific type of photography to be able to be directed there easily without having to look at a mix of other kinds of photography. I will provide a few files to use as placeholders. I have already purchased the bramkelletphotography.example domain name. A Wix website would be great because I am most familiar with it but I am open to anything.

Industry/Entity Type

Photographer

Number of Pages Required

5+ page

Requirements
Must have
• Landing Page and e-commerce

```html
<!DOCTYPE html>
<html lang="en">
<head>
<meta charset="utf-8">
<title>Bram Kellet Photography</title>
<link rel="stylesheet" href="https://fonts.googleapis.com/css2?family=Lato:wght@400;700&family=Poppins:wght@400&family=Great+Vibes&family=Arimo:wght@400;500&display=swap">
<style>
  :root {
    --ink: #1f1f1f;
    --ink-soft: #3a3a3a;
    --accent: #4e5a7e;
    --rule: #bdbdbd;
    --muted: #8a8a8a;
    --paper: #ffffff;
  }
  * { box-sizing: border-box; margin: 0; padding: 0; }
  html, body { width: 909px; height: 1200px; overflow: hidden; background: var(--paper); }
  body { position: relative; font-family: "Lato", sans-serif; color: var(--ink); }

  .brand { position: absolute; left: 84px; top: 24px; width: 164px; text-align: center; }
  .brand-name { font-family: "Lato", sans-serif; font-size: 15px; color: var(--accent); letter-spacing: 0.3px; }
  .brand-line { font-family: "Lato", sans-serif; font-size: 5px; color: var(--accent); margin-top: 3px; letter-spacing: 0.3px; }

  .site-nav { position: absolute; left: 56px; top: 116px; width: 200px; list-style: none; text-align: center; }
  .site-nav li { height: 37.7px; font-size: 13px; line-height: 18px; color: var(--ink); }
  .site-nav li.is-current { color: var(--accent); }

  .hero { position: absolute; left: 273px; top: 0; width: 636px; height: 415px;
    background: linear-gradient(100deg, #f1ece8 0%, #e5dcd6 30%, #c9b6a6 55%, #6b5548 78%, #2e2a2c 100%); }
  .hero-title { position: absolute; left: 24px; top: 118px; font-family: "Great Vibes", cursive; font-size: 34px; color: #111; }
  .hero-kicker { position: absolute; left: 24px; top: 170px; font-size: 18.5px; color: var(--ink-soft); letter-spacing: 0.2px; }
  .hero-copy { position: absolute; left: 25px; top: 201px; width: 260px; font-family: "Poppins", sans-serif; font-size: 10.3px; line-height: 19.5px; color: var(--ink-soft); }
  .hero-button { position: absolute; left: 21px; top: 252px; width: 190px; height: 40px; border: 1.5px solid #fff;
    font-size: 13px; color: var(--accent); display: flex; align-items: center; justify-content: center; letter-spacing: 0.2px; }

  .featured-heading { position: absolute; left: 271px; top: 476px; font-family: "Arimo", sans-serif; font-size: 22px; font-weight: 400; color: var(--ink); }
  .gallery-card { position: absolute; width: 267px; }
  .gallery-photo { width: 267px; height: 247px; }
  .gallery-label { margin-top: 10px; text-align: center; font-family: "Arimo", sans-serif; font-size: 13px; color: var(--ink); letter-spacing: 0.2px; }
  .gallery-label.is-bold { font-weight: 500; }
  .card-nature { left: 273px; top: 518px; }
  .card-weddings { left: 557px; top: 518px; }
  .card-portraits { left: 273px; top: 808px; }
  .card-architecture { left: 557px; top: 808px; }
  .photo-nature { background: linear-gradient(180deg, #3e4a38 0%, #5f6b55 45%, #c98a4a 60%, #eef1f4 80%); }
  .photo-weddings { background: radial-gradient(circle at 50% 45%, #2a3147 0%, #6b5a4a 35%, #a08670 70%, #7e6a5a 100%); }
  .photo-portraits { background: linear-gradient(135deg, #2a2a2a 0%, #9a9a9a 40%, #c9c9c9 60%, #5a5a5a 100%); }
  .photo-architecture { background: linear-gradient(180deg, #e8eaec 0%, #a45a42 40%, #b9ab99 65%, #cfcbc4 100%); }

  .footer-rule { position: absolute; left: 87px; top: 1141px; width: 740px; height: 1px; background: var(--rule); }
  .copyright { position: absolute; left: 273px; top: 1161px; font-family: "Poppins", sans-serif; font-size: 10.5px; color: var(--ink-soft); }
  .social-links { position: absolute; left: 784px; top: 1163px; display: flex; gap: 7px; }
  .social-links span { width: 10px; height: 10px; border-radius: 50%; background: var(--muted); }
</style>
</head>
<body>
  <header class="brand">
    <div class="brand-name">Bram Kellet Photography</div>
    <div class="brand-line">creating lasting images of every moment</div>
  </header>

  <ul class="site-nav">
    <li class="is-current">Home</li>
    <li>Galleries</li>
    <li>Pricing</li>
    <li>Book Now</li>
    <li>Testimonials</li>
    <li>Faq</li>
    <li>Contact</li>
  </ul>

  <section class="hero" role="img" aria-label="Cover photo of a bride and groom kissing outdoors">
    <h1 class="hero-title">Bram Kellet Photography</h1>
    <p class="hero-kicker">CAPTURE THE MOMENTS</p>
    <p class="hero-copy">Lorem ipsum dolor sit amet, consectetur iscing elit, sed do eiusmod tempor incididunt ut</p>
    <div class="hero-button">MAKE AN APPOINTMENT</div>
  </section>

  <h2 class="featured-heading">Featured Photos</h2>

  <figure class="gallery-card card-nature">
    <div class="gallery-photo photo-nature" role="img" aria-label="Red fox sitting in snow beneath evergreen trees"></div>
    <figcaption class="gallery-label">NATURE</figcaption>
  </figure>
  <figure class="gallery-card card-weddings">
    <div class="gallery-photo photo-weddings" role="img" aria-label="Wedding rings resting on a granite stone"></div>
    <figcaption class="gallery-label">WEDDINGS</figcaption>
  </figure>
  <figure class="gallery-card card-portraits">
    <div class="gallery-photo photo-portraits" role="img" aria-label="Black and white portrait study of folded arms"></div>
    <figcaption class="gallery-label">PORTRAITS</figcaption>
  </figure>
  <figure class="gallery-card card-architecture">
    <div class="gallery-photo photo-architecture" role="img" aria-label="Modern brick and stone building exterior"></div>
    <figcaption class="gallery-label is-bold">ARCHITECTURE</figcaption>
  </figure>

  <div class="footer-rule"></div>
  <p class="copyright">Copyright © 2020 Bramkelletphotography. All Rights Reserved.</p>
  <div class="social-links" aria-label="Social links"><span></span><span></span><span></span></div>
</body>
</html>
```